BOLD & MINIMALIST DESIGN NEEDED

We want a very bold but minimalistic business card design that is impactful and utilizes both sides of the business card. Our current logo is included for your use.

We want bold fonts and good use of negative space. We don't want the logo to overpower the design.

Target Market(s)

Professionals who are building new commercial buildings.

Industry/Entity Type

Construction

Contact Information for Business Card

Name, Title, email, office phone, cell phone, website

Font styles to use
Serif
Sans Serif

Requirements
Must have
• Bold design!

```html
<!DOCTYPE html>
<html lang="en">
<head>
<meta charset="utf-8">
<title>Summitcrest Design + Build — Business Card</title>
<link rel="stylesheet" href="https://fonts.googleapis.com/css2?family=Poppins:wght@400;500;600;800&display=swap">
<style>
  :root {
    --bg: #2b2b2b;
    --ink: #0a0a0a;
    --paper: #ffffff;
    --green: #8cc63f;
    --text: #1a1a1a;
  }
  * { box-sizing: border-box; margin: 0; padding: 0; }
  html, body { width: 1200px; height: 875px; overflow: hidden; }
  body {
    background: var(--bg);
    font-family: "Poppins", sans-serif;
    display: flex;
    align-items: center;
    justify-content: center;
    gap: 40px;
  }
  .card {
    position: relative;
    width: 540px;
    height: 309px;
    border-radius: 16px;
    overflow: hidden;
    box-shadow: 0 18px 40px rgba(0,0,0,0.45);
  }
  .card svg.shape { position: absolute; inset: 0; width: 100%; height: 100%; }

  /* Back side */
  .card--back { background: var(--ink); }
  .card--back .brand {
    position: absolute;
    right: 36px;
    top: 74px;
    color: var(--paper);
    text-align: right;
    z-index: 1;
  }
  .brand__name {
    font-weight: 800;
    font-size: 34px;
    letter-spacing: 0.5px;
    line-height: 1;
    text-transform: uppercase;
  }
  .brand__tag {
    font-weight: 800;
    font-size: 13px;
    letter-spacing: 5px;
    margin-top: 6px;
    text-transform: uppercase;
  }

  /* Front side */
  .card--front { background: var(--paper); }
  .card--front .brand {
    position: absolute;
    left: 38px;
    top: 150px;
    color: var(--ink);
    display: flex;
    align-items: center;
    gap: 10px;
    z-index: 1;
  }
  .brand__mark {
    width: 16px;
    height: 16px;
    background: var(--green);
    flex: none;
  }
  .card--front .brand__name { font-size: 26px; }
  .card--front .brand__tag { font-size: 10px; letter-spacing: 4px; }

  .divider {
    position: absolute;
    left: 300px;
    top: 40px;
    width: 1px;
    height: 150px;
    background: var(--green);
  }
  .contact {
    position: absolute;
    left: 318px;
    top: 34px;
    color: var(--text);
    z-index: 1;
  }
  .contact__name {
    color: var(--green);
    font-weight: 600;
    font-size: 22px;
    line-height: 1.1;
  }
  .contact__title { font-size: 12px; margin-bottom: 10px; }
  .contact__list { list-style: none; font-size: 11.5px; line-height: 1.55; }
  .contact__list li { display: flex; align-items: center; gap: 7px; }
  .contact__list svg { width: 10px; height: 10px; fill: var(--green); flex: none; }
  .contact__address { font-size: 11.5px; line-height: 1.4; margin-top: 10px; font-weight: 500; }
</style>
</head>
<body>

  <section class="card card--back" aria-label="Card back">
    <svg class="shape" viewBox="0 0 540 309" preserveAspectRatio="none" aria-hidden="true">
      <path d="M0 282 Q 260 178 540 172 L540 188 Q 280 196 0 309 Z" fill="var(--paper)"/>
    </svg>
    <div class="brand">
      <div class="brand__name">Summitcrest</div>
      <div class="brand__tag">Design + Build</div>
    </div>
  </section>

  <section class="card card--front" aria-label="Card front">
    <svg class="shape" viewBox="0 0 540 309" preserveAspectRatio="none" aria-hidden="true">
      <path d="M60 309 Q 300 180 540 150 L540 309 Z" fill="var(--green)"/>
    </svg>

    <div class="brand">
      <span class="brand__mark"></span>
      <div>
        <div class="brand__name">Summitcrest</div>
        <div class="brand__tag">Design + Build</div>
      </div>
    </div>

    <div class="divider"></div>

    <div class="contact">
      <div class="contact__name">Daniel Reyes</div>
      <div class="contact__title">Head contractor</div>
      <ul class="contact__list">
        <li><svg viewBox="0 0 10 10"><path d="M2 0.5 L4 2.5 L3 3.8 Q4.5 6 6.2 7 L7.5 6 L9.5 8 L8 9.5 Q3 9 0.5 2 Z"/></svg>555.214.3300</li>
        <li><svg viewBox="0 0 10 10"><path d="M2.5 0 H7.5 V10 H2.5 Z M3.5 1 V8 H6.5 V1 Z"/></svg>555-214-3301</li>
        <li><svg viewBox="0 0 10 10"><path d="M0 2 H10 V8 H0 Z M0.8 2.6 L5 5.6 L9.2 2.6 V2.9 L5 6.2 L0.8 2.9 Z" fill-rule="evenodd"/></svg>hello@scdb-build.com</li>
        <li><svg viewBox="0 0 10 10"><circle cx="5" cy="5" r="4.5"/></svg>www.scdb-build.com</li>
      </ul>
      <div class="contact__address">412 Ridgeway Rd.<br>Cedar Falls, GA 30999</div>
    </div>
  </section>

</body>
</html>
```